Visitenkarten-Design für Sonnen-/Fensterschutz
Zielgruppe
KLW GmbH ist eine Firma, die Sonnenschutz und Fensterschutz anbieten.
'Ihr kompetenter Partner in Sachen Sonnenschutz- , Fenster- und Türtechnik. Sie erhalten echtes Handwerk aus dem Mühlviertel zu fairen Preisen.'
Unsere Zielgruppe sind Personen mit Haus, die am Land leben.
Firmenname: KLW GmbH
Slogan: Fenster & Sonnenschutz
Aufgabenstellung
Hier befindet sich das Logodesign: https://dx.qv/t-QwLpo7RbNs
Bitte ein schlichtes Design bereitstellen mit einer Dummy-Person:
Jonas Weidlinger + Telefonnummer + Email
Die finalen Daten bitte erst am Schluss berücksichtigen (für Gewinnerdesign)
Gerne auch hintern + vorne bedruckbar bereitstellen.

```html
<!DOCTYPE html>
<html lang="de">
<head>
<meta charset="utf-8">
<title>KLW GmbH – Visitenkarte Vorder- und Rückseite</title>
<link rel="stylesheet" href="https://fonts.googleapis.com/css2?family=Open+Sans:wght@400;600;700&display=swap">
<style>
  :root {
    --page-bg: #ecebe9;
    --card-white: #ffffff;
    --card-grey: #e4e4e4;
    --brand-orange: #e8672c;
    --brand-orange-light: #f08a5d;
    --brand-red: #d9262a;
    --brand-red-deep: #b81f24;
    --ink: #1d1d1d;
    --ink-soft: #3a3a3a;
    --faint: rgba(0, 0, 0, 0.05);
  }
  * { box-sizing: border-box; margin: 0; padding: 0; }
  html, body {
    width: 1200px; height: 800px; overflow: hidden;
    background: var(--page-bg);
    font-family: "Open Sans", Arial, sans-serif;
  }
  .sheet {
    width: 1200px; height: 800px;
    display: flex; align-items: center; justify-content: center; gap: 60px;
  }
  .card {
    position: relative; width: 520px; height: 336px; overflow: hidden;
    border-radius: 4px;
    box-shadow: 0 14px 30px rgba(0,0,0,0.18);
  }

  /* Vorderseite */
  .card--front {
    background: linear-gradient(135deg, var(--card-white) 30%, var(--card-grey) 100%);
  }
  .front__watermark {
    position: absolute; right: -20px; top: 40px;
    font-size: 170px; font-weight: 700; line-height: 1;
    color: var(--faint); letter-spacing: -4px;
  }
  .front__identity {
    position: absolute; left: 40px; top: 52px;
    display: flex; align-items: center; gap: 18px;
  }
  .front__wordmark {
    font-size: 17px; font-weight: 700; color: var(--brand-orange);
  }
  .front__divider {
    width: 2px; height: 62px; background: var(--brand-orange);
    transform: skewX(-20deg);
  }
  .front__name {
    font-size: 26px; font-weight: 600; color: var(--brand-orange); line-height: 1.15;
  }
  .front__role {
    font-size: 24px; font-weight: 400; color: var(--ink); line-height: 1.15;
  }
  .front__contacts {
    position: absolute; right: 40px; top: 150px;
    list-style: none; display: flex; flex-direction: column; gap: 9px;
  }
  .contact {
    display: flex; align-items: center; gap: 10px;
    font-size: 13.5px; color: var(--ink-soft);
  }
  .contact--web { font-weight: 700; color: var(--ink); }
  .contact svg { width: 14px; height: 14px; flex: none; }
  .front__brandbox {
    position: absolute; left: 0; bottom: 24px;
    width: 210px; height: 96px;
    background: var(--brand-red);
    display: flex; flex-direction: column; justify-content: center; padding-left: 26px;
    color: var(--card-white);
  }
  .brandbox__name { font-size: 24px; font-weight: 700; line-height: 1.1; }
  .brandbox__tagline { font-size: 9px; font-weight: 700; letter-spacing: 0.6px; margin-top: 4px; }
  .front__band {
    position: absolute; left: 0; right: 0; bottom: 0; height: 24px;
    background: linear-gradient(90deg, var(--brand-orange) 0%, var(--brand-orange-light) 40%, var(--card-white) 100%);
  }

  /* Rückseite */
  .card--back {
    background: linear-gradient(135deg, var(--brand-orange-light) 0%, var(--brand-orange) 40%, var(--brand-red) 75%, var(--brand-red-deep) 100%);
    color: var(--card-white);
  }
  .back__watermark {
    position: absolute; left: -14px; bottom: -30px;
    font-size: 190px; font-weight: 700; line-height: 1; letter-spacing: -6px;
    color: rgba(255,255,255,0.9);
  }
  .back__brand {
    position: absolute; right: 36px; top: 56px; text-align: right;
  }
  .back__name { font-size: 38px; font-weight: 700; line-height: 1.05; }
  .back__tagline { font-size: 12.5px; font-weight: 700; letter-spacing: 0.8px; margin-top: 6px; }
</style>
</head>
<body>
<main class="sheet">

  <section class="card card--front" aria-label="Vorderseite">
    <div class="front__watermark" aria-hidden="true">KLW</div>

    <div class="front__identity">
      <span class="front__wordmark">KLW GmbH</span>
      <span class="front__divider" aria-hidden="true"></span>
      <div>
        <p class="front__name">Jonas Weidlinger</p>
        <p class="front__role">Director</p>
      </div>
    </div>

    <ul class="front__contacts">
      <li class="contact">
        <svg viewBox="0 0 16 16" aria-hidden="true"><path fill="#d9262a" d="M3.5 1.5l2.5 0 1 3.5-1.7 1.2a8 8 0 0 0 4.5 4.5L11 9l3.5 1v2.5c0 1-1 2-2 2C6.5 14.5 1.5 9.5 1.5 3.5c0-1 1-2 2-2z"/></svg>
        0111 4826039175
      </li>
      <li class="contact">
        <svg viewBox="0 0 16 16" aria-hidden="true"><rect x="1" y="3" width="14" height="10" rx="1" fill="#d9262a"/><path d="M1.5 3.5L8 9l6.5-5.5" fill="none" stroke="#fff" stroke-width="1.3"/></svg>
        jonas@musterseite.de
      </li>
      <li class="contact contact--web">
        <svg viewBox="0 0 16 16" aria-hidden="true"><circle cx="8" cy="8" r="7" fill="#d9262a"/><path d="M1 8h14M8 1c-3 3.5-3 10.5 0 14M8 1c3 3.5 3 10.5 0 14" fill="none" stroke="#fff" stroke-width="1"/></svg>
        www.musterseite.de
      </li>
    </ul>

    <div class="front__brandbox">
      <span class="brandbox__name">KLW GmbH</span>
      <span class="brandbox__tagline">FENSTER &amp; SONNENSCHUTZ</span>
    </div>
    <div class="front__band" aria-hidden="true"></div>
  </section>

  <section class="card card--back" aria-label="Rückseite">
    <div class="back__watermark" aria-hidden="true">KLW</div>
    <div class="back__brand">
      <p class="back__name">KLW GmbH</p>
      <p class="back__tagline">FENSTER &amp; SONNENSCHUTZ</p>
    </div>
  </section>

</main>
</body>
</html>
```